Brightway Haus Inc. Business Card Design

Brightway Haus Inc. is in search of a great clean design for our business cards!

Looking to incorporate our full logo and watermark on side one (however, I am open to having the text and watermark separated within the design.)

On side two, I am looking to have contact information (Name, Position, Phone #, Email, Website (www.thebrightwayhaus.ca). Can have the logo and/or watermark as part of the design if applicable.

Please add tagline "Where Shine Counts" on either side 1 or 2. This tagline can be in a sans serif, serif or cursive font as long as it compliments overall design. Capitalization can be title or sentence case depending on how it fits within the design.

Get creative!! Looking for a clean, crisp, premium design! Looking for a glossy card finish with spot UV features when printed. Cards will also be printed with rounded corners. Standard dimensions (3.5 x 2).

Target Market(s)

B2B - primary clients are business owners or property management corporations. (residential jobs are few and far between)

Industry/Entity Type

Business

Contact Information for Business Card

- clean, crisp design
- double sided
- spot UV accents and glossy finish upon printing
- standard business card size (3.5 x 2) with rounded corners
- please see project description for requirements per side

Font styles to use
Sans Serif

Requirements
Must have
• - adequate bleeds with print ready files
• - cohesive design elements between side 1 & 2
• - spot UV elements (can be on both sides or just one, use your discretion)
• - colour pallet should match the logo file provided
• - incorporate tagline "where shine counts" (this tagline can be in a serif or sans serif font as long as it is complimentary to the overall design.
Nice to have
• - Premium elements with a clean design
Should not have
• - Please omit cartoon or whimsical like designs, think premium.
• - Colours should not stray from the pallet of the provided logo.

```html
<!DOCTYPE html>
<html lang="en">
<head>
<meta charset="utf-8">
<title>Brightway Haus Inc. Business Cards</title>
<link href="https://fonts.googleapis.com/css2?family=Montserrat:wght@500;600;700;800&family=Roboto:wght@400;500&display=swap" rel="stylesheet">
<style>
  :root {
    --teal: #29b6b2;
    --teal-soft: #d6f0ef;
    --navy: #1f2b6e;
    --ink: #4a4f55;
    --card-dark: #1b1f22;
    --watermark-dark: #1f3b3a;
    --paper: #fbfbfb;
    --stage: #e7e8ea;
  }
  * { box-sizing: border-box; margin: 0; padding: 0; }
  html, body { width: 1200px; height: 911px; overflow: hidden; background: var(--stage); }
  .stage { position: relative; width: 1200px; height: 911px; }

  .card {
    position: absolute; top: 118px; width: 380px; height: 665px;
    border-radius: 26px; overflow: hidden;
    box-shadow: 0 10px 30px rgba(0,0,0,.18);
  }
  .card--contact { left: 170px; background: var(--paper); }
  .card--brand { left: 650px; background: var(--card-dark); }

  /* contact side */
  .contact-watermark {
    position: absolute; left: 40px; top: 250px; width: 300px; height: 360px;
    border-radius: 150px 150px 40px 40px;
    background: linear-gradient(180deg, rgba(41,182,178,.05), var(--teal-soft) 60%, rgba(41,182,178,.08));
  }
  .brand-name {
    font-family: "Montserrat", sans-serif; font-weight: 800; color: var(--navy);
    letter-spacing: .5px; text-transform: uppercase;
  }
  .contact-logo {
    position: absolute; top: 96px; left: 0; right: 0;
    display: flex; justify-content: center; align-items: center; gap: 10px;
    font-size: 27px;
  }
  .logo-dot { width: 16px; height: 16px; border-radius: 50%; background: var(--teal); }
  .contact-body {
    position: absolute; top: 270px; left: 0; right: 0; text-align: center;
    font-family: "Roboto", sans-serif; color: var(--ink);
  }
  .person-name {
    font-family: "Montserrat", sans-serif; font-weight: 700; font-size: 22px;
    color: var(--teal); text-transform: uppercase; letter-spacing: .5px;
  }
  .person-title {
    font-family: "Montserrat", sans-serif; font-weight: 600; font-size: 15px;
    color: var(--navy); text-transform: uppercase; margin-top: 2px;
  }
  .contact-list { list-style: none; margin-top: 14px; }
  .contact-list li { font-size: 15px; line-height: 1; }
  .contact-list svg { display: block; margin: 8px auto 7px; width: 14px; height: 14px; fill: var(--teal); }
  .contact-list .address { line-height: 1.3; }

  /* brand side */
  .brand-watermark {
    position: absolute; left: 120px; top: 160px; width: 230px; height: 360px;
    border-radius: 0 0 0 160px;
    background: linear-gradient(160deg, var(--watermark-dark), #203a39);
  }
  .brand-watermark-accent {
    position: absolute; left: 40px; top: 330px; width: 120px; height: 150px;
    border-radius: 80px 0 0 80px; background: #2a2e31;
  }
  .brand-lockup {
    position: absolute; left: 190px; top: 332px;
    transform: translate(-50%, -50%) rotate(90deg);
    display: flex; flex-direction: column; align-items: center; white-space: nowrap;
  }
  .brand-lockup .brand-name { font-size: 44px; color: var(--teal); line-height: 1; }
  .tagline {
    font-family: "Roboto", sans-serif; font-size: 14px; color: #e9eaeb;
    letter-spacing: 9px; margin-top: 12px; order: -1; margin-bottom: 12px;
  }
</style>
</head>
<body>
<main class="stage">
  <section class="card card--contact" aria-label="Contact side">
    <div class="contact-watermark" role="img" aria-label="Faint brand watermark"></div>
    <div class="contact-logo"><span class="logo-dot"></span><span class="brand-name">Brightway Haus Inc.</span></div>
    <div class="contact-body">
      <p class="person-name">Daniel Reyes</p>
      <p class="person-title">CEO/Founder</p>
      <ul class="contact-list">
        <li><svg viewBox="0 0 24 24"><path d="M6.6 10.8a15 15 0 006.6 6.6l2.2-2.2a1 1 0 011-.25 11.4 11.4 0 003.6.57 1 1 0 011 1V20a1 1 0 01-1 1A17 17 0 013 4a1 1 0 011-1h3.5a1 1 0 011 1c0 1.25.2 2.45.57 3.57a1 1 0 01-.25 1z"/></svg>604 318 2275</li>
        <li><svg viewBox="0 0 24 24"><path d="M7 1h10a2 2 0 012 2v18a2 2 0 01-2 2H7a2 2 0 01-2-2V3a2 2 0 012-2zm0 3v15h10V4z"/></svg>604 552 7190</li>
        <li><svg viewBox="0 0 24 24"><path d="M6 2h12v5H6zM3 8h18a1 1 0 011 1v8h-4v5H6v-5H2V9a1 1 0 011-1zm5 8v4h8v-4z"/></svg>604 771 3086</li>
        <li><svg viewBox="0 0 24 24"><path d="M2 5h20v14H2zm2 2v.5l8 5 8-5V7z"/></svg>hello@brightwayhaus.ca</li>
        <li class="address"><svg viewBox="0 0 24 24"><path d="M12 2a7 7 0 017 7c0 5-7 13-7 13S5 14 5 9a7 7 0 017-7zm0 4a3 3 0 100 6 3 3 0 000-6z"/></svg>4210 Juniper Lane<br>Halden, Alberta 21486</li>
      </ul>
    </div>
  </section>

  <section class="card card--brand" aria-label="Brand side">
    <div class="brand-watermark" role="img" aria-label="Faint brand watermark"></div>
    <div class="brand-watermark-accent" role="img" aria-label="Faint brand watermark detail"></div>
    <div class="brand-lockup">
      <span class="brand-name">Brightway Haus Inc.</span>
      <span class="tagline">Where Shine Counts</span>
    </div>
  </section>
</main>
</body>
</html>
```